Real estate broker business card

Want a modern celan but effective business card for my residential and commercial real estate business. I want the back of the card to advertise my services and to capture business. I have attached the back of my current business card fore ideas
Updates

Logos, photo and text updates added! Added Saturday, September 3, 2016

Project Deadline Extended Reason: LOGOS, PHOTOS AND TEST JUST UPLOADED! I'M READY TO PICK A DESIGN! THANK YOU! Added Saturday, September 3, 2016

Target Market(s)

home buyers and seller. commercial buyers and sellers

Industry/Entity Type

Real Estate

Contact Information for Business Card

must have my contact information and my photo

Requirements
Must have
• Carla Ventrino
• Owner & Qualifying Broker
• Ventrino Real Estate Services
• 505.718.2094
• carla@ventrinohomes.example
• www.ventrinohomes.example
Nice to have
• metallic
• Business capture text: " Don't buy or lease property without someone looking out for your best interests. I will represent you on your home or investment purchase for FREE!"
• "Home owners, call today to receive a FREE market analysis for your homes value!

```html
<!DOCTYPE html>
<html lang="en">
<head>
<meta charset="utf-8">
<title>Ventrino Real Estate Services – Business Card</title>
<link href="https://fonts.googleapis.com/css2?family=Cinzel:wght@500&family=Open+Sans:ital,wght@0,400;0,600;1,400&display=swap" rel="stylesheet">
<style>
  :root{
    --bg:#2b2d31;
    --teal:#0f7d8c;
    --teal-deep:#0a6472;
    --teal-light:#1496a6;
    --ink:#2a2a2a;
    --paper-top:#f4f5f6;
    --paper-bottom:#d9dbdd;
    --white:#ffffff;
    --photo-dark:#3a2c27;
    --photo-light:#cfc8c4;
  }
  *{box-sizing:border-box;margin:0;padding:0}
  html,body{width:1200px;height:864px;overflow:hidden}
  body{background:var(--bg);position:relative;font-family:"Open Sans",Arial,sans-serif}

  .card{position:absolute;left:320px;width:560px;height:320px;overflow:hidden;border-radius:3px;box-shadow:0 10px 24px rgba(0,0,0,.45)}
  .card--back{top:80px;background:linear-gradient(135deg,var(--teal-light),var(--teal) 45%,var(--teal-deep))}
  .card--front{top:464px;background:linear-gradient(160deg,var(--paper-top),var(--paper-bottom))}

  .back__curves{position:absolute;inset:0}
  .back__brand{position:absolute;top:34px;left:0;right:0;text-align:center;color:var(--white);
    font-family:"Cinzel",Georgia,serif;font-weight:500}
  .back__brand-name{display:block;font-size:44px;line-height:1;letter-spacing:3px}
  .back__brand-sub{display:block;font-size:15px;line-height:1.4;letter-spacing:4px;margin-top:4px}
  .back__pitch{position:absolute;top:132px;left:80px;right:80px;text-align:center;color:var(--white);
    font-style:italic;font-size:13.5px;line-height:1.35}
  .back__pitch p+p{margin-top:12px}

  .front__photo{position:absolute;left:0;top:0;width:250px;height:320px;
    background:linear-gradient(170deg,var(--photo-dark) 0%,#6e5a52 45%,var(--photo-light) 100%);
    border-top-right-radius:60px}
  .front__brand{position:absolute;top:40px;right:30px;display:flex;align-items:center;gap:10px;
    color:var(--teal);font-family:"Cinzel",Georgia,serif;font-weight:500;text-align:left}
  .front__brand-name{display:block;font-size:32px;line-height:1;letter-spacing:2px}
  .front__brand-sub{display:block;font-size:11.5px;line-height:1.4;letter-spacing:3px;margin-top:3px}
  .front__brand-dot{width:40px;height:40px;border-radius:50%;background:var(--teal);flex:none}
  .front__details{position:absolute;right:30px;bottom:14px;text-align:right;color:var(--ink)}
  .front__name{color:var(--teal);font-weight:600;font-size:18px;line-height:1.2}
  .front__title{font-size:14.5px;line-height:1.3}
  .front__company{color:var(--teal);font-weight:600;font-size:15px;margin-top:10px;line-height:1.3}
  .front__contact{list-style:none;font-size:14px;line-height:1.4}
  .front__contact li{display:flex;justify-content:flex-end;align-items:center;gap:8px}
  .front__contact svg{width:12px;height:12px;fill:var(--teal);flex:none}
</style>
</head>
<body>

<section class="card card--back" aria-label="Card back">
  <svg class="back__curves" viewBox="0 0 560 320" aria-hidden="true">
    <path d="M160 320 C140 200 170 60 330 0 L560 0 L560 320 Z" fill="rgba(255,255,255,.05)"/>
    <path d="M230 320 C220 220 260 120 360 80 C450 50 520 80 560 110 L560 320 Z" fill="rgba(0,0,0,.06)"/>
  </svg>
  <h1 class="back__brand"><span class="back__brand-name">VENTRINO</span><span class="back__brand-sub">REAL ESTATE SERVICES</span></h1>
  <div class="back__pitch">
    <p>Don't buy or lease property without someone looking out for your best interests. I will represent you on your home or investment purchase for FREE!</p>
    <p>Home owners, call today to receive a FREE market analysis for your homes value!</p>
  </div>
</section>

<section class="card card--front" aria-label="Card front">
  <div class="front__photo" role="img" aria-label="Portrait photo of Carla Ventrino"></div>
  <div class="front__brand"><span class="front__brand-dot"></span><span><span class="front__brand-name">VENTRINO</span><span class="front__brand-sub">REAL ESTATE SERVICES</span></span></div>
  <div class="front__details">
    <p class="front__name">Carla Ventrino</p>
    <p class="front__title">Owner &amp; Qualifying Broker</p>
    <p class="front__company">Ventrino Real Estate Services</p>
    <ul class="front__contact">
      <li>505.718.2094
        <svg viewBox="0 0 24 24" aria-hidden="true"><path d="M6.6 10.8a15 15 0 0 0 6.6 6.6l2.2-2.2c.3-.3.7-.4 1-.2 1.1.4 2.3.6 3.6.6.6 0 1 .4 1 1V20c0 .6-.4 1-1 1A17 17 0 0 1 3 4c0-.6.4-1 1-1h3.5c.6 0 1 .4 1 1 0 1.3.2 2.5.6 3.6.1.3 0 .7-.2 1z"/></svg></li>
      <li>carla@ventrinohomes.example
        <svg viewBox="0 0 24 24" aria-hidden="true"><path d="M2 5h20v14H2z"/><path d="M2 5l10 8 10-8" fill="none" stroke="#fff" stroke-width="2"/></svg></li>
      <li>www.ventrinohomes.example
        <svg viewBox="0 0 24 24" aria-hidden="true"><circle cx="12" cy="12" r="10"/></svg></li>
    </ul>
  </div>
</section>

</body>
</html>
```